Pine leaf & Snapvista ad needed

I am in need of a simple static image ad to be used for Pineleaf & Snapvista. A photo of a nice roof on a nice house. "Instant Satellite Roof Estimates" "Your house, your time & instant estimate" . Our logo file is here: https://www.filecrate-example.net/share/q73kdm41xv9wpz2tbn8hs/JKsT4mWQpZ2xYcVn8bRfL6d?key=wm5tz81qvjx3c7bnd0ke9fa4r&v=0

Multiple variations will be purchased.

```html
<!DOCTYPE html>
<html lang="en">
<head>
<meta charset="UTF-8">
<title>Instant Satellite Roof Estimates – Crestline Roofing</title>
<link href="https://fonts.googleapis.com/css2?family=Outfit:wght@500;600&family=Roboto:wght@700&display=swap" rel="stylesheet">
<style>
  :root {
    --backdrop-light: #f4f6f7;
    --backdrop-edge: #c9d3d8;
    --card-grey: #e6e6e6;
    --panel-blue: #4b97ae;
    --panel-blue-deep: #4a93ab;
    --headline-white: #ffffff;
    --headline-yellow: #f4e05a;
    --logo-ink: #161616;
  }
  * { margin: 0; padding: 0; box-sizing: border-box; }
  html, body {
    width: 1200px;
    height: 1155px;
    overflow: hidden;
  }
  body {
    background: radial-gradient(ellipse at center, var(--backdrop-light) 55%, var(--backdrop-edge) 100%);
    position: relative;
  }
  .ad-card {
    position: absolute;
    left: 95px;
    top: 69px;
    width: 1010px;
    height: 1017px;
    overflow: hidden;
    background: var(--card-grey);
    box-shadow: 0 6px 24px rgba(60, 80, 90, 0.18);
  }
  .ad-art {
    position: absolute;
    inset: 0;
    width: 1010px;
    height: 1017px;
  }
  .headline {
    position: absolute;
    left: 440px;
    top: 395px;
    font-family: "Outfit", sans-serif;
    font-weight: 600;
    font-size: 56px;
    line-height: 81px;
    letter-spacing: 0.5px;
    text-transform: uppercase;
    color: var(--headline-white);
  }
  .headline .accent { color: var(--headline-yellow); display: block; }
  .tagline {
    position: absolute;
    left: 440px;
    top: 652px;
    font-family: "Roboto", sans-serif;
    font-weight: 700;
    font-size: 40px;
    line-height: 62px;
    color: var(--headline-white);
  }
  .brand {
    position: absolute;
    left: 32px;
    top: 866px;
    font-family: "Outfit", sans-serif;
    font-weight: 500;
    color: var(--logo-ink);
    line-height: 1;
  }
  .brand-name {
    display: block;
    font-size: 62px;
    letter-spacing: 1px;
  }
  .brand-trade {
    display: block;
    text-align: right;
    font-size: 24px;
    letter-spacing: 4px;
    margin-top: 4px;
  }
</style>
</head>
<body>
  <main class="ad-card">
    <svg class="ad-art" viewBox="0 0 1010 1017" xmlns="http://www.w3.org/2000/svg">
      <defs>
        <linearGradient id="house-photo-tones" x1="0" y1="0" x2="0" y2="1">
          <stop offset="0" stop-color="#b9c0c6"/>
          <stop offset="0.18" stop-color="#4a4f55"/>
          <stop offset="0.55" stop-color="#2c3034"/>
          <stop offset="0.8" stop-color="#6a4a35"/>
          <stop offset="1" stop-color="#4f6a3e"/>
        </linearGradient>
        <linearGradient id="panel-fade" x1="0" y1="0" x2="0" y2="1">
          <stop offset="0" stop-color="#4b97ae" stop-opacity="0.72"/>
          <stop offset="0.6" stop-color="#4b97ae" stop-opacity="0.9"/>
          <stop offset="1" stop-color="#4a93ab" stop-opacity="1"/>
        </linearGradient>
      </defs>
      <rect class="hero-photo" role="img" aria-label="Photo of a dark two-storey lakeside house with a standing-seam metal roof, stone chimneys, wraparound porch and wooden steps" x="0" y="0" width="1010" height="780" fill="url(#house-photo-tones)"/>
      <path class="grey-base" d="M0,728 Q230,660 520,712 L520,1017 L0,1017 Z" fill="#e6e6e6"/>
      <path class="blue-panel" d="M864,0 C600,120 400,300 413,520 C420,760 470,900 506,1017 L1010,1017 L1010,0 Z" fill="url(#panel-fade)"/>
    </svg>

    <h1 class="headline">
      Instant
      <span class="accent">Satellite</span>
      <span class="accent">Roof Estimates</span>
    </h1>
    <p class="tagline">Your House, Your Time<br>&amp; Instant Estimate.</p>

    <div class="brand">
      <span class="brand-name">CRESTLINE</span>
      <span class="brand-trade">ROOFING</span>
    </div>
  </main>
</body>
</html>
```